A clean crisp business card for a Landscape Construction company. Designed to be easy to read contact/ info and also be appealing/interesting, unlike a traditional business card.

Industry/Entity Type

Landscape Construction

Contact Information for Business Card

Company name : Brambleford Landscape Construction, phone number: (877) 62Vista, website:Bramblefordyards.example, Email, sales@bramblefordyards.example

Requirements
Nice to have
• Luxurious finishes/ details…. Icons or emblems next to contact info
Should not have
• Clipart or general pictures

```html
<!DOCTYPE html>
<html lang="en">
<head>
<meta charset="UTF-8">
<title>Brambleford Landscape Construction – Business Card</title>
<link href="https://fonts.googleapis.com/css2?family=Cinzel:wght@400;600&family=Arimo:wght@400&display=swap" rel="stylesheet">
<style>
  :root {
    --backdrop: #1e1e1e;
    --card-white: #ffffff;
    --brand-blue: #1769c0;
    --brand-green: #8cc63f;
    --ink: #1a1a1a;
    --rule: #b5b5b5;
  }
  * { box-sizing: border-box; margin: 0; padding: 0; }
  html, body {
    width: 1200px; height: 900px; overflow: hidden;
    background: var(--backdrop);
  }
  .canvas { position: relative; width: 1200px; height: 900px; }

  .card {
    position: absolute;
    width: 560px; height: 320px;
    box-shadow: 0 18px 40px rgba(0,0,0,0.55);
  }

  /* Front: contact side */
  .card-front {
    left: 130px; top: 100px;
    background: var(--card-white);
    border-left: 3px solid var(--brand-blue);
    border-bottom: 3px solid var(--brand-blue);
  }
  .identity {
    position: absolute; left: 0; right: 0; top: 82px;
    text-align: center;
  }
  .person-name {
    font-family: 'Cinzel', serif;
    font-size: 30px; font-weight: 400; letter-spacing: 1px;
    line-height: 1;
  }
  .person-name .first { color: var(--brand-blue); }
  .person-name .last { color: var(--brand-green); }
  .person-title {
    font-family: 'Arimo', Arial, sans-serif;
    font-size: 14px; color: var(--ink); margin-top: 4px;
  }
  .details {
    position: absolute; left: 0; right: 0; top: 160px;
    display: flex; justify-content: center; align-items: stretch;
    font-family: 'Arimo', Arial, sans-serif;
    font-size: 13.5px; color: var(--ink); line-height: 1.45;
  }
  .address { text-align: right; padding-right: 16px; }
  .divider { width: 1px; background: var(--rule); }
  .contact-list { list-style: none; padding-left: 14px; }
  .contact-list li { display: flex; align-items: center; gap: 7px; }
  .contact-list svg { width: 13px; height: 13px; flex: none; }
  .contact-list .accent { color: var(--brand-blue); }

  /* Back: brand side */
  .card-back {
    left: 510px; top: 480px;
    background: var(--brand-blue);
    display: flex; flex-direction: column; align-items: center; justify-content: center;
  }
  .wordmark {
    font-family: 'Cinzel', serif; font-weight: 400;
    color: var(--card-white); text-align: center;
    display: flex; flex-direction: column; align-items: center; gap: 8px;
  }
  .wordmark .dot {
    width: 18px; height: 18px; border-radius: 50%;
    background: var(--card-white); margin-bottom: 10px;
  }
  .wordmark .name { font-size: 44px; letter-spacing: 2px; line-height: 1; }
  .wordmark .tagline { font-size: 17px; letter-spacing: 6px; }
</style>
</head>
<body>
<main class="canvas">

  <section class="card card-front" aria-label="Business card front">
    <div class="identity">
      <h1 class="person-name"><span class="first">Owen</span> <span class="last">Hartley</span></h1>
      <p class="person-title">Managing Director</p>
    </div>
    <div class="details">
      <address class="address" style="font-style:normal">
        421, Address line<br>goes here 45452<br>Country Name
      </address>
      <span class="divider"></span>
      <ul class="contact-list">
        <li>
          <svg viewBox="0 0 16 16" aria-hidden="true"><path fill="var(--brand-blue)" d="M3.6 1.5l2.2 2.6-1.3 1.6c.9 2 2.3 3.5 4.3 4.4l1.6-1.3 2.6 2.2-1.3 2.3C6.5 13 2.8 9.3 1.3 4z"/></svg>
          (877) 62Vista
        </li>
        <li>
          <svg viewBox="0 0 16 16" aria-hidden="true"><rect x="1" y="3" width="14" height="10" fill="var(--brand-blue)"/><path d="M1.5 3.5L8 9l6.5-5.5" fill="none" stroke="#fff" stroke-width="1.2"/></svg>
          sales@bramblefordyards.example
        </li>
        <li>
          <svg viewBox="0 0 16 16" aria-hidden="true"><g fill="none" stroke="var(--brand-blue)" stroke-width="1.3"><circle cx="8" cy="8" r="6.5"/><ellipse cx="8" cy="8" rx="3" ry="6.5"/><path d="M1.5 8h13M2.5 4.8h11M2.5 11.2h11"/></g></svg>
          <span><span class="accent">Bramblefordyards</span>.example</span>
        </li>
      </ul>
    </div>
  </section>

  <section class="card card-back" aria-label="Business card back">
    <div class="wordmark">
      <span class="dot" aria-hidden="true"></span>
      <span class="name">Brambleford</span>
      <span class="tagline">Landscape Construction</span>
    </div>
  </section>

</main>
</body>
</html>
```